Business Cards

I am a landscape designer and I am hired to do over the top landscapes!
I pay attention to detail and do everything from growing my own orchids and Fruits and Vegetables.
I build ponds water features. I do Landscape Lighting and Specialize in Drip Irrigation for New Landscapes.
I am looking for something with a picture of one of my landscapes and pictures of Orchids on the back so I can work on growing my Orchid business.
I like the plastic cards.
I like Saturation
I like color and I want something that really sticks out!
I will attach a few pics!
Thanks
Corey
A Verdant Terrace LLC
Corey Halvorsen
Orchids & Organic Farming
Landscaping Made Simple
561-555-0147
Averdantterrace@mailbrook.net
West Palm Beach FL

Target Market(s)

I work for Wealthy Clients who want unique designs and enjoy rare plants.
I am the goto guy for tropical and rare plants
Cool Designs
Orchids
Interior Decorating
Exterior Lighting
Organic Farming
People who appreciate plants

Industry/Entity Type

Landscape

Font styles to use
Decorative

Requirements
Must have
• COLOR COLOR COLOR
Saturation
Sleek and Clean
Should not have
• tacky

```html
<!DOCTYPE html>
<html lang="en">
<head>
<meta charset="utf-8">
<title>A Verdant Terrace LLC – Business Cards</title>
<link rel="stylesheet" href="https://fonts.googleapis.com/css2?family=Rokkitt:wght@600;700&family=Oswald:wght@600&family=Arimo:wght@400&display=swap">
<style>
  :root {
    --backdrop: #ece7e0;
    --card-border: #ffffff;
    --text-white: #ffffff;
    --tagline-yellow: #ffd21a;
    --brand-green: #1e9a3a;
    --brand-violet: #3b0ee6;
    --contact-red: #ff1508;
    --contact-orange: #ff5a00;
  }
  * { margin: 0; padding: 0; box-sizing: border-box; }
  html, body {
    width: 1200px;
    height: 900px;
    overflow: hidden;
    background: var(--backdrop);
  }
  .card {
    position: absolute;
    left: 272px;
    width: 654px;
    height: 372px;
    background: var(--card-border);
    padding: 23px 24px;
    box-shadow: 0 3px 10px rgba(0,0,0,0.18);
  }
  .card--front { top: 43px; }
  .card--back { top: 480px; }
  .card__photo {
    width: 100%;
    height: 100%;
  }
  .photo--orchid {
    background:
      radial-gradient(ellipse at 50% 95%, #ffd400 0%, #ffe600 25%, transparent 55%),
      radial-gradient(ellipse at 15% 60%, #ffe000 0%, #ff9a00 30%, transparent 55%),
      radial-gradient(ellipse at 88% 55%, #ffe800 0%, #ff7a10 35%, transparent 60%),
      radial-gradient(ellipse at 50% 10%, #ffb000 0%, #ff5a20 40%, transparent 65%),
      linear-gradient(135deg, #e84020 0%, #ffcc00 45%, #5a7a9a 100%);
  }
  .photo--garden {
    background:
      radial-gradient(ellipse at 15% 25%, #c8884a 0%, transparent 30%),
      radial-gradient(ellipse at 85% 45%, #e02a3a 0%, transparent 25%),
      radial-gradient(ellipse at 90% 85%, #5a4a4a 0%, transparent 30%),
      radial-gradient(ellipse at 30% 85%, #4aa83a 0%, transparent 40%),
      linear-gradient(160deg, #2f8a3a 0%, #4fb04a 40%, #2a7a30 70%, #3a5a3a 100%);
  }
  .panel {
    position: absolute;
    left: 162px;
    top: 86px;
    width: 330px;
    height: 199px;
    text-align: center;
    color: var(--text-white);
    overflow: hidden;
  }
  .panel--brand {
    background: linear-gradient(90deg, var(--brand-green) 0%, var(--brand-violet) 100%);
    display: flex;
    align-items: center;
    justify-content: center;
  }
  .brand-name {
    font-family: "Rokkitt", serif;
    font-weight: 700;
    font-size: 50px;
    line-height: 60px;
    letter-spacing: 0.5px;
    text-transform: uppercase;
    white-space: nowrap;
  }
  .panel--contact {
    top: 87px;
    background: linear-gradient(90deg, var(--contact-red) 0%, var(--contact-orange) 100%);
    padding-top: 12px;
  }
  .person-name {
    font-family: "Rokkitt", serif;
    font-weight: 600;
    font-size: 33px;
    line-height: 42px;
    letter-spacing: 0.5px;
    text-transform: uppercase;
    white-space: nowrap;
    text-decoration: underline;
    text-decoration-thickness: 2px;
    text-underline-offset: 3px;
  }
  .tagline {
    margin-top: 4px;
    font-family: "Oswald", sans-serif;
    font-weight: 600;
    font-size: 13.5px;
    line-height: 18px;
    letter-spacing: 0.6px;
    color: var(--tagline-yellow);
    text-transform: uppercase;
  }
  .contact-list {
    list-style: none;
    margin-top: 28px;
    font-family: "Arimo", sans-serif;
    font-size: 18px;
    line-height: 20.5px;
    white-space: nowrap;
  }
</style>
</head>
<body>
  <section class="card card--front">
    <div class="card__photo photo--orchid" role="img" aria-label="Close-up photograph of a saturated yellow and orange orchid bloom"></div>
    <div class="panel panel--brand">
      <h1 class="brand-name">A Verdant<br>Terrace<br>LLC</h1>
    </div>
  </section>

  <section class="card card--back">
    <div class="card__photo photo--garden" role="img" aria-label="Photograph of a lush tropical landscape with palms, colourful foliage and a paver path"></div>
    <div class="panel panel--contact">
      <h2 class="person-name">Corey Halvorsen</h2>
      <p class="tagline">Orchids &amp; Organic Farming<br>Landscaping Made Easy</p>
      <ul class="contact-list">
        <li>561-555-0147</li>
        <li>Averdantterrace@mailbrook.net</li>
        <li>West Palm Beach FL</li>
      </ul>
    </div>
  </section>
</body>
</html>
```